Torvane Email Signature Banners – Fabrication Capability Series

www.Torvane.com.au is an Australian engineering and fabrication company specialising in fabrication and welding of :
steel piping spools,
skids and frames,
small volume process steel tanks
and general steel fabrication
We require four distinct banner designs for use in Microsoft Lintaro email signatures. Each banner will highlight a specific capability while maintaining a consistent brand identity.
Deliverables
Four banners total:
Piping Spools Fabrication – focus on precision welding and stainless steel pipework
Skid & Frames Fabrication – highlight skid systems and structural frames
Small Steel Tanks Fabrication – show fabricated tanks and workshop craftsmanship
General Fabrication Solutions – broad steel fabrication theme for company-wide use
Dimensions: 600–700 px wide × 100 px high
Format: PNG (preferred), small file size prefered
Resolution: 72 dpi
Background: non-transparent, industrial or workshop setting
Text examples:
1. Piping Spools Fabrication
Option A: “Expert Fabrication Solutions for Process Piping”
Option B: “Precision Welding for Complex Systems”
Option C: “Delivering Quality in Every Spool”
Option D: “Engineered for Flow, Built for Strength”
2. Skid & Frames Fabrication
Option A: “Custom Engineered Modular Systems”
Option B: “Built Strong. Designed Smart.”
Option C: “Reliable Frames for Industrial Performance”
Option D: “Modular Fabrication for Seamless Integration”
3. Small Steel Tanks Fabrication
Option A: “Precision Built for Your Needs”
Option B: “Compact Strength. Proven Durability.”
Option C: “Fabricated for Performance and Longevity”
Option D: “Small Tanks. Big Reliability.”
4. General Fabrication Solutions
Option A: “Quality Craftsmanship, Proven Results”
Option B: “Your Partner in Precision Fabrication”
Option C: “Engineering Excellence in Every Weld”
Option D: “Australian Fabrication. Global Standards.”
Style Direction
Clean, professional, and engineering‑focused
Use Torvane brand colours
Blend photo realism with vector clarity (no heavy gradients)
Include subtle industrial textures or workshop imagery
Typography: bold sans‑serif, legible at small scale
Usage Context
These banners will appear at the bottom of staff email signatures via Lintaro Email Signature Tool for Microsoft 365, so clarity and fast loading are essential. No Logo is required in the banners.
Reference
Existing Torvane signature is attached. Colour palette to match the signature style and logo.
Target Market(s)
Engineering and construction companies,
Industry/Entity Type
Engineering fabrication design
Look and feel

```html
<!DOCTYPE html>
<html lang="en">
<head>
<meta charset="utf-8">
<title>Torvane Signature Banners</title>
<link rel="stylesheet" href="https://fonts.googleapis.com/css2?family=Arimo:wght@700&display=swap">
<style>
  :root {
    --board: #c9c9c9;
    --banner-bg: #fbfbfb;
    --title-blue: #1fa3dd;
    --subtitle-grey: #8b8b8b;
    --brand-blue: #0b6fd8;
    --brand-blue-light: #2d97e6;
    --steel-grey: #d4d6d9;
    --steel-grey-dark: #b9bcc0;
    --photo-steel: #4c6a86;
    --photo-workshop: #7d8a95;
    --photo-tank: #5a7da3;
    --photo-cleanroom: #8fa8c2;
  }
  html, body {
    margin: 0;
    padding: 0;
    width: 1200px;
    height: 555px;
    overflow: hidden;
    background: var(--board);
  }
  .board {
    position: relative;
    width: 1200px;
    height: 555px;
  }
  .banner {
    position: absolute;
    left: 106px;
    width: 988px;
    height: 138px;
    background: var(--banner-bg);
    overflow: hidden;
  }
  .banner--spools { top: 85px; }
  .banner--tanks { top: 309px; }
  .banner-shadow {
    position: absolute;
    left: 250px;
    width: 700px;
    height: 18px;
    border-radius: 50%;
    background: radial-gradient(ellipse at center, rgba(0,0,0,0.32) 0%, rgba(0,0,0,0) 70%);
  }
  .banner-shadow--spools { top: 220px; }
  .banner-shadow--tanks { top: 446px; }
  .banner-art {
    position: absolute;
    inset: 0;
    width: 988px;
    height: 138px;
  }
  .banner-copy {
    position: absolute;
    left: 20px;
    top: 0;
    height: 138px;
    display: flex;
    flex-direction: column;
    justify-content: center;
    font-family: "Arimo", Arial, sans-serif;
    font-weight: 700;
  }
  .banner-title {
    margin: 0;
    color: var(--title-blue);
    font-size: 31px;
    line-height: 1.1;
    letter-spacing: 0.2px;
  }
  .banner-tagline {
    margin: 4px 0 0;
    color: var(--subtitle-grey);
    font-size: 21px;
    line-height: 1.2;
  }
</style>
</head>
<body>
<div class="board">

  <div class="banner-shadow banner-shadow--spools"></div>
  <section class="banner banner--spools">
    <svg class="banner-art" viewBox="0 0 700 98" preserveAspectRatio="none">
      <polygon points="380,0 470,0 440,20 400,20" fill="var(--steel-grey)"/>
      <polygon points="440,0 520,0 505,14 455,14" fill="var(--steel-grey-dark)"/>
      <polygon points="605,0 700,0 700,98 660,98 690,60" fill="var(--brand-blue)"/>
      <polygon points="640,0 700,0 700,40" fill="var(--brand-blue-light)"/>
      <polygon points="540,85 700,85 700,98 525,98" fill="var(--brand-blue)"/>
      <g role="img" aria-label="Photo of stacked steel pipes in a fabrication workshop">
        <polygon points="430,15 545,15 600,82 470,82" fill="var(--photo-steel)"/>
      </g>
      <polygon points="545,15 555,15 612,82 600,82" fill="#ffffff"/>
      <g role="img" aria-label="Photo of process plant pipework and equipment">
        <polygon points="555,15 660,15 685,82 612,82" fill="var(--photo-workshop)"/>
      </g>
      <polygon points="660,85 672,85 680,98 668,98" fill="#ffffff"/>
    </svg>
    <div class="banner-copy">
      <h2 class="banner-title">PIPING SPOOLS FABRICATION</h2>
      <p class="banner-tagline">Expert Fabrication Solutions for Process Piping</p>
    </div>
  </section>

  <div class="banner-shadow banner-shadow--tanks"></div>
  <section class="banner banner--tanks">
    <svg class="banner-art" viewBox="0 0 700 98" preserveAspectRatio="none">
      <defs>
        <clipPath id="bannerClip"><rect width="700" height="98"/></clipPath>
      </defs>
      <g clip-path="url(#bannerClip)">
        <path d="M640,0 L700,0 L700,98 L640,98 Q670,49 640,0 Z" fill="var(--brand-blue-light)"/>
        <circle cx="565" cy="50" r="66" fill="var(--brand-blue)"/>
        <g role="img" aria-label="Photo of a worker in protective clothing beside stainless steel tanks">
          <circle cx="565" cy="50" r="58" fill="var(--photo-cleanroom)"/>
        </g>
        <circle cx="478" cy="48" r="40" fill="var(--brand-blue-light)"/>
        <circle cx="478" cy="48" r="35" fill="#ffffff"/>
        <g role="img" aria-label="Photo of a welder working on a steel tank">
          <circle cx="478" cy="48" r="31" fill="var(--photo-tank)"/>
        </g>
      </g>
    </svg>
    <div class="banner-copy">
      <h2 class="banner-title">SMALL STEEL TANKS FABRICATION</h2>
      <p class="banner-tagline">Fabricated for Performance and Longevity</p>
    </div>
  </section>

</div>
</body>
</html>
```